Schlichtes Design für Malerbetrieb
Zielgruppe
Wir sind ein mittelgroßer Malerbetrieb in München mit umfangreichem Leistungsspektrum.
Unsere Hauptleistungen sind: Fassadenrenovierung, Altbausanierung, Betoninstandsetzung, Balkonabdichtung (kein Neubau!).
Unsere Zielgruppen sind: Hausverwaltungen, Firmen und Privatpersonen.
Unsere Kunden schätzen: Konstruktive Organisation und Planung im Vorfeld, Zuverlässigkeit, saubere Arbeitsweise, dauerhafte Balkonabdichtungen.
Aufgabenstellung
Wir möchten eine langlebige, stilvolle, minimalistische Homepage.
Wir möchten von der bestehenden Homepage nur die Schriftart für unseren Firmennamen (Century Gothic) und wenn möglich (nicht zwingend), irgendwo das florale Muster einbauen. Corporate-Design haben wir nicht.
Farbtöne: Firmennamen Orange (hellorange bis erdiges Orange möglich, da sind wir nicht fixiert) , einen dunklen Hintergrundfarbton (Petrol-Blaugrau ?) mit gelbem (neon bis senfgelb) Akzent (Linien), Blumenmuster weiß, grau.
Dies sind nur unsere Ideen. Wir sind aber auch absolut offen für eure Profi-Ideen.
Wir möchten uns von den unzähligen langweiligen 'Pinselseiten mit veralteten Bilder' unserer Kollegen interessant und mit Stil abheben.
Eher nach dem Motto 'weniger ist mehr'.
Einen positiven, sympathischen Eindruck geben und unsere Leistungen in den Vordergrund bringen.
Da wir viele Stammkunden haben, betreiben wir kein Social-Media und möchten dies vorerst auch nicht tun.
Die Seite wird in den nächsten Jahren nicht verändert, höchstens die Bilder aktualisiert.
Die Texte haben wir alle selbst entworfen und möchten wir so übernehmen.
Die Galerien sollen unkompliziert anzuschauen sein.
Uns gefällt die Struktur und Schlichtheit von https://vaartmolen.nl/ oder Timbra.de gut und wir mögen Vintage-Grafiken gerne.
Einerseits darf die Seite geradlinig, andererseits aber auch rund und floral wirken.

```html
<!DOCTYPE html>
<html lang="de">
<head>
<meta charset="utf-8">
<title>Kolbrit – Malerbetrieb München</title>
<link rel="stylesheet" href="https://fonts.googleapis.com/css2?family=Questrial&family=Montserrat:ital,wght@0,300;0,400;0,500;0,600;1,400;1,500;1,600;1,700&display=swap">
<style>
:root{
  --orange:#f2a21c;
  --header:#5f5c5c;
  --blush:#e8dcdd;
  --blush-light:#f3ecec;
  --project-bg:#ede4e5;
  --footer:#675d5e;
  --text:#3b3b3b;
  --white:#ffffff;
  --card-gray:#6b6a6a;
}
*{box-sizing:border-box;margin:0;padding:0}
html,body{width:1200px;height:4232px;overflow:hidden}
body{position:relative;background:var(--white);font-family:"Montserrat",sans-serif;color:var(--text)}
.abs{position:absolute}

/* header */
.site-header{left:0;top:0;width:1200px;height:72px;background:var(--header);z-index:3}
.brand{left:82px;top:20px;font-family:"Montserrat",sans-serif;font-weight:600;font-size:28px;color:var(--white);letter-spacing:0;line-height:32px;display:flex;align-items:center;gap:10px}
.brand-mark{width:12px;height:12px;background:var(--white)}
.nav{right:60px;top:28px;display:flex;gap:32px;font-family:"Questrial",sans-serif;font-size:12px;color:#eee;letter-spacing:.5px}
.nav .active{color:var(--orange)}
.hero{left:0;top:72px;width:1200px;height:484px;background:linear-gradient(100deg,#d9d6da 0%,#8bbfc6 30%,#41c3cd 55%,#5ccad3 80%,#2f6d86 100%)}
.hero-text{left:0;top:225px;width:1200px;text-align:center;color:#fff;font-family:"Questrial",sans-serif;text-shadow:0 2px 6px rgba(0,0,0,.25)}
.hero-kicker{font-size:28px;letter-spacing:3px}
.hero-title{font-family:"Montserrat",sans-serif;font-weight:600;font-size:46px;line-height:56px;letter-spacing:1px;margin-top:14px}
.side-tools{right:0;top:145px;width:60px}
.side-tools div{height:60px;margin-bottom:3px;background:rgba(120,110,110,.75);display:flex;align-items:center;justify-content:center}

/* intro */
.intro{left:0;top:556px;width:1200px;height:424px;background:var(--blush)}
.intro-img{left:140px;top:44px;width:355px;height:345px;background:radial-gradient(circle at 50% 50%,#f0a640 0%,#e9c79a 40%,var(--blush) 70%)}
.intro-card{left:598px;top:52px;width:602px;height:316px;background:var(--white);box-shadow:0 2px 10px rgba(0,0,0,.08)}
.intro-card .rule{left:84px;top:42px;width:1px;height:232px;background:#ccc}
.intro-card p{left:117px;top:40px;width:380px;font-size:12px;line-height:26px;color:#666}
.more{font-style:italic;font-size:12px;color:#444}

/* section titles */
.section-title{left:0;width:1200px;text-align:center;font-family:"Montserrat",sans-serif;font-weight:300;font-size:28px;color:#333;letter-spacing:.5px}
.section-title::after{content:"";display:block;width:185px;height:2px;background:#555;margin:8px auto 0}

/* services */
.tile{overflow:hidden}
.tile .label{position:absolute;left:0;right:0;bottom:22px;text-align:center;color:#fff;font-family:"Questrial",sans-serif;font-size:23px;letter-spacing:1px}
.tile .label::before{content:"";display:block;width:260px;height:2px;background:#fff;margin:0 auto 14px}
.tile-beton-img{left:0;top:1128px;width:401px;height:136px;background:linear-gradient(120deg,#5a5450,#a59d97 60%,#cfcac6)}
.tile-beton{left:0;top:1264px;width:401px;height:236px;background:var(--card-gray);color:#fff;text-align:center}
.plus{left:174px;top:-27px;width:54px;height:54px;border-radius:50%;background:#fff;color:#333;font-size:38px;line-height:50px;text-align:center}
.tile-beton h3{position:absolute;top:48px;width:100%;font-family:"Questrial",sans-serif;font-weight:400;font-size:23px;letter-spacing:.5px}
.tile-beton h3::after{content:"";display:block;width:200px;height:1px;background:#ddd;margin:8px auto 0}
.tile-beton p{position:absolute;top:96px;width:100%;font-size:11px;line-height:17px}
.tile-farbe{left:403px;top:1128px;width:406px;height:372px;background:linear-gradient(150deg,#f3eeee,#ecdcd8 50%,#e6d0c6)}
.tile-maler{left:809px;top:1128px;width:391px;height:372px;background:linear-gradient(150deg,#f4c15a,#eeb13c 60%,#d9a03e)}
.tile-balkon{left:0;top:1500px;width:594px;height:246px;background:linear-gradient(140deg,#1f4e5e,#2f6d7a 50%,#3d7f86)}
.tile-waerme{left:595px;top:1500px;width:605px;height:246px;background:linear-gradient(150deg,#a9a09a,#c9c0ba 50%,#d9d2cd)}

/* features */
.features{left:0;top:1776px;width:1200px;height:217px;display:flex}
.feature{position:relative;text-align:center;font-size:14px;font-weight:500;line-height:23px;color:#333;padding-top:28px}
.feature + .feature{border-left:1px solid #ddd}
.feature svg{display:block;margin:0 auto 28px}

/* successes */
.erfolge{left:0;top:2016px;width:1200px;height:542px;background:linear-gradient(180deg,var(--blush-light),#f6f0f0 60%,var(--blush-light))}
.quote{font-style:italic;font-size:16px;line-height:22px;color:#555}
.quote cite{display:block;margin-top:24px;font-weight:600;color:#444}

/* training */
.ausbildung{left:0;top:2560px;width:1200px;height:360px;background:linear-gradient(90deg,#f5b233,#f3ad2c 45%,#f0c05a 75%,#e9cb8a)}
.ausbildung-card{left:0;top:46px;width:510px;height:268px;background:var(--white)}
.ausbildung-card p{left:117px;top:60px;width:340px;font-size:11px;line-height:26px;color:#666}
.ausbildung-quote{left:570px;top:92px;width:500px;text-align:center;color:#fff;font-style:italic;font-weight:700;font-size:23px;line-height:35px}

/* projects */
.projekte{left:0;top:2920px;width:1200px;height:738px;background:var(--project-bg)}
.proj-side{top:202px;height:220px}
.proj-left{left:84px;width:233px;background:linear-gradient(160deg,#4a4842,#6d6a62)}
.proj-right{left:896px;width:245px;background:linear-gradient(160deg,#3c3638,#7a7070)}
.proj-main{left:317px;top:144px;width:579px;height:326px;background:linear-gradient(180deg,#e9e7e2,#d6d2ca 60%,#9c7f60);box-shadow:0 3px 12px rgba(0,0,0,.2)}

/* contact */
.footer-bg{left:0;top:3658px;width:1200px;height:574px;background:var(--footer)}
.contact{left:163px;top:3477px;width:873px;height:551px;background:var(--white)}
.contact h2{left:27px;top:28px;font-family:"Questrial",sans-serif;font-weight:400;font-size:40px;color:var(--orange);letter-spacing:1px}
.field-label{left:32px;font-size:11px;color:#aaa}
.field{left:32px;width:440px;height:40px;border:1px solid #e6e6e6}
.contact .divider{left:506px;top:40px;width:1px;height:440px;background:#ddd}
.contact-brand{left:541px;top:40px;font-family:"Montserrat",sans-serif;font-weight:600;font-size:30px;color:#333;line-height:34px;display:flex;align-items:center;gap:10px}
.contact-brand .brand-mark{background:#333}
.contact-info{left:541px;top:108px;width:320px;font-size:11px;line-height:27px;color:#333}
.contact-info .soft{color:#aaa}
.site-footer{left:161px;top:4140px;font-size:12px;line-height:21px;color:#c8bebe}
.footer-links{left:894px;top:4124px;display:grid;grid-template-columns:97px auto;font-size:11px;line-height:21px;color:#c8bebe}
</style>
</head>
<body>

<header class="abs site-header">
  <div class="abs brand"><span class="brand-mark"></span>kolbrit</div>
  <nav class="abs nav"><span class="active">HOME</span><span>ÜBER UNS</span><span>SERVICES</span><span>AUSBILDUNG</span><span>REFERENZEN</span><span>KONTAKT</span></nav>
</header>

<section class="abs hero" role="img" aria-label="Foto: Maler streicht eine Wand türkis mit der Rolle"></section>
<div class="abs hero-text">
  <div class="hero-kicker">IHR SPEZIALIST FÜR</div>
  <div class="hero-title">MALERARBEITEN, BALKONABDICHTUNG,<br>WÄRMEDEMMUNG &amp; CO.</div>
</div>
<div class="abs side-tools">
  <div><svg width="30" height="22" viewBox="0 0 30 22" fill="none" stroke="#f2a21c" stroke-width="1.5"><rect x="1" y="1" width="28" height="20"/><path d="M1 1l14 11L29 1"/></svg></div>
  <div><svg width="28" height="28" viewBox="0 0 28 28" fill="none" stroke="#f2a21c" stroke-width="1.5"><path d="M6 2l5 6-3 3c2 4 5 7 9 9l3-3 6 5-3 4C12 25 3 16 2 5z"/></svg></div>
  <div><svg width="28" height="28" viewBox="0 0 28 28" fill="none" stroke="#f2a21c" stroke-width="1.8"><circle cx="11" cy="11" r="8"/><path d="M17 17l9 9"/></svg></div>
</div>

<section class="abs intro">
  <div class="abs intro-img" role="img" aria-label="Illustration: Hocker mit Farbeimern, Pinseln und Farbrollen"></div>
  <div class="abs intro-card">
    <div class="abs rule"></div>
    <p class="abs">Setzen Sie auf Qualität, Sorgfalt und Zuverlässigkeit – Setzen Sie auf uns! Mit jahrzehntelanger Erfahrung und einem hohen Maß an Fachwissen begeistern wir Neu- und Stammkunden und legen uns für Sie ins Zeug. Entdecken Sie unser umfangreiches Leistungsspektrum und profitieren auch Sie von professionellen, dauerhaften Ergebnissen!<br><span class="more">Über uns ›</span></p>
  </div>
</section>

<h2 class="abs section-title" style="top:1032px">UNSERE LEISTUNGEN</h2>

<div class="abs tile-beton-img" role="img" aria-label="Foto: Arbeiter auf Betonfläche"></div>
<div class="abs tile-beton">
  <div class="abs plus">+</div>
  <h3>BETONINSTANDSETZUNG</h3>
  <p>Hier entsteht eine kurze Beschreibung<br>unserer Leistung im Bereich Beton</p>
  <svg class="abs" style="left:226px;top:164px" width="32" height="38" viewBox="0 0 32 38" fill="none" stroke="#fff" stroke-width="1.6" stroke-linejoin="round"><path d="M11 20V4a2.5 2.5 0 015 0v12l2-1a2.5 2.5 0 014 1v1a2.5 2.5 0 014 1v1a2.5 2.5 0 014 1v7c0 6-4 10-10 10h-3c-4 0-7-3-9-7l-4-8a2.5 2.5 0 014-3z"/></svg>
</div>
<div class="abs tile tile-farbe" role="img" aria-label="Foto: Hände mit Farbfächer"><div class="label">FARBGESTALTUNG</div></div>
<div class="abs tile tile-maler" role="img" aria-label="Foto: Maler streicht eine Decke"><div class="label">MALERARBEITEN</div></div>
<div class="abs tile tile-balkon" role="img" aria-label="Foto: Balkon mit Hängesessel und Pflanzen"><div class="label">BALKONABDICHTUNG</div></div>
<div class="abs tile tile-waerme" role="img" aria-label="Foto: Hausfassade bei Dämmarbeiten"><div class="label">WÄRMEDEMMUNG</div></div>

<section class="abs features">
  <div class="feature" style="width:324px">
    <svg width="48" height="46" viewBox="0 0 48 46" fill="none" stroke="#f2a21c" stroke-width="1.8"><path d="M28 4l16 16-8 4-12-12z"/><path d="M24 12L10 30l6 6 20-12"/><path d="M10 30l-6 12 12-6"/></svg>
    Konstruktive Organisation<br>&amp; Planung</div>
  <div class="feature" style="width:294px">
    <svg width="48" height="46" viewBox="0 0 48 46" fill="none" stroke="#f2a21c" stroke-width="1.8"><rect x="4" y="32" width="40" height="10"/><path d="M4 32V6l40 26"/><path d="M4 32L30 10M4 32l16-24M4 32l34-14"/></svg>
    Hohe technische<br>Erfahrung &amp; faire Beratung</div>
  <div class="feature" style="width:270px">
    <svg width="48" height="46" viewBox="0 0 48 46" fill="none" stroke="#f2a21c" stroke-width="1.8"><rect x="24" y="4" width="18" height="10" transform="rotate(40 33 9)"/><path d="M26 18L8 38l4 4 18-20"/></svg>
    Dauerhaft schöne Ergebnisse<br>in bester Qualität</div>
  <div class="feature" style="width:312px">
    <svg width="48" height="46" viewBox="0 0 48 46" fill="none" stroke="#f2a21c" stroke-width="1.8"><path d="M4 18L24 4l20 14"/><rect x="8" y="16" width="32" height="27"/><rect x="14" y="22" width="6" height="6"/><rect x="28" y="22" width="6" height="6"/><rect x="20" y="32" width="8" height="11"/></svg>
    Umfassender,<br>kundenfreundlicher<br>Rundum-Service</div>
</section>

<section class="abs erfolge">
  <h2 class="abs section-title" style="top:42px">UNSERE ERFOLGE</h2>
  <blockquote class="abs quote" style="left:117px;top:158px;width:318px">“Diesen Betrieb können wir nur mit Bestnoten ausstatten! Das Preis-Leistungsverhältnis stimmt. Das Team berät einen sehr gut und findet für die Ideen seiner Kunden eine praktikable Lösung. Sie arbeiten akkurat, pünktlich und sauber. TOP gerne jederzeit wieder..”<cite>Miriam Haller, Privat</cite></blockquote>
  <blockquote class="abs quote" style="left:470px;top:252px;width:318px">“Ich habe mit der Kolbrit GmbH sehr gute Erfahrungen gemacht. Ich musste meinen Balkon aufgrund von undichten Stellen neu abdichten lassen. Alles prima gelaufen. Die Arbeiter waren immer pünktlich und freundlich, mit der Ausführung der Arbeiten war ich sehr zufrieden.”<cite>Jonas Brenner, Privat</cite></blockquote>
  <blockquote class="abs quote" style="left:817px;top:158px;width:322px">“Ich kann diese Firma nur wärmstens empfehlen. Der Monteur, der bei mir war, war sehr kompetent. Das Preis/Leistungsverhältnis ist meines Erachtens nach sehr gut. Sehr schnelle Schadensbeseitigung. Sehr gute Kommunikation. Ich selber würde die Firma immer wieder bestellen.”<cite>Peter Ostwalder, Privat</cite></blockquote>
</section>

<section class="abs ausbildung" role="img" aria-label="Foto: Auszubildender bei der Arbeit, orange getönt">
  <div class="abs ausbildung-card">
    <p class="abs">Wir möchten junge Menschen auf ihrem Weg in den Beruf fördern: Du bist motiviert, interessiert und zielbewusst? Dann bewirb Dich jetzt um eine unserer beliebten Ausbildungsstellen!<br><span class="more" style="font-size:11px;line-height:40px">Zu unseren Ausbildungsinfos ›</span></p>
  </div>
  <p class="abs ausbildung-quote">"Es war eine super gute Zeit.<br>Ich habe mich gut aufgenommen und unterstützt gefühlt. Die Ausbildung ist sehr vielseitig, fachlich gut aufgestellt und wirklich interessant."</p>
</section>

<section class="abs projekte">
  <h2 class="abs section-title" style="top:60px">UNSERE PROJEKTE</h2>
  <div class="abs proj-side proj-left" role="img" aria-label="Foto: Altbaufassade"></div>
  <div class="abs proj-side proj-right" role="img" aria-label="Foto: Ladeneinrichtung"></div>
  <div class="abs proj-main" role="img" aria-label="Foto: renovierter heller Altbauraum mit Tisch und Stühlen">
    <svg class="abs" style="left:536px;top:140px" width="24" height="44" viewBox="0 0 24 44" fill="none" stroke="#fff" stroke-width="2"><path d="M3 2l18 20L3 42"/></svg>
  </div>
</section>

<div class="abs footer-bg"></div>
<section class="abs contact">
  <h2 class="abs">PREISANFRAGE</h2>
  <div class="abs field-label" style="top:90px">Vor- und Nachname</div>
  <div class="abs field" style="top:105px"></div>
  <div class="abs field-label" style="top:180px">E-Mail Adresse</div>
  <div class="abs field" style="top:196px"></div>
  <div class="abs field-label" style="top:262px">Ihre Nachricht</div>
  <div class="abs field" style="top:280px;height:240px"></div>
  <div class="abs divider"></div>
  <div class="abs contact-brand"><span class="brand-mark"></span>kolbrit</div>
  <div class="abs contact-info">
    <p class="soft">Als sachkundiger und verantwortungsbewusster Dienstleister für Malerarbeiten und Co stehen wir Ihnen gerne zur Verfügung.</p>
    <p style="margin-top:18px">Haben Sie Fragen oder benötigen weitere Informationen nehmen Sie gerne Kontakt mit uns auf.</p>
    <p style="margin-top:18px;line-height:21px">TELEFON &amp; FAX<br>089 41 27 60 | 089 41 27 69</p>
    <p style="margin-top:24px;line-height:21px">EMAIL<br>info@kolbrit-maler.de</p>
    <p style="margin-top:16px;line-height:21px">Werkstatt: Lindenhofweg 42 | 81371 München<br>Büro: Almrauschstraße 7 | 82049 Pullach</p>
  </div>
</section>

<footer class="abs site-footer">© 2019 KOLBRIT GmbH. All rights reserved.<br>Almrauschstraße 7<br>82049 Pullach</footer>
<nav class="abs footer-links">
  <span>Preisanfrage</span><span>Jobs</span>
  <span>Standorte</span><span>Impressum</span>
  <span>Service</span><span>Datenschutz</span>
  <span>Umfang</span><span>Rechtliche Hinweise</span>
</nav>

</body>
</html>
```